I need a complete stationary pack for a real estate office that sells and manages residential proper

We need a stationary design pack for my real estate office called ‘brightkeyhomes’ that is in Queensland Australia. My offices are both in suburban and coastal locations in the south west corner of Queensland at the Coral Bay Shore and Brisbane.
We predominately manage real estate on behalf of owners and sell property in the residential sector.
I have attached a copy of our existing design of my business card and do like the current concept/layout. In saying this you may be able to use this existing theme across to the other items required or see opportunity on how to improve what I have already.
I would like to see concepts for the following products:
- Letterhead
- Fax header
- Business cards
- Email signature
- With complements slips and
- Envelopes
I have attached our current logo that was designed by Artfolder and the font is Prelo.

I am looking for a contemporary design that is professional and reflects trust and professionalism. I am currently using the logo with a black background on some material as per the following link

http://www.plotlisting.com.au/property/for-sale/house/qld/merridale/?adid=4827305118&sp=7

I have posted another job 517362 for signage and the company car signage done too if you are interested.

Please do not hesitate to contact me should you have any questions. Thank you.

Target Market(s)

Western speaking people aged from 25 to 60 from modest backgrounds to well off individuals

Industry/Entity Type

Real Estate

Requirements
Must have
• Professional in appearance, show a mature and trustworthy image
Should not have
• As there is good colour with the logo, i am do not want over the top designs or colours

```html
<!DOCTYPE html>
<html lang="en">
<head>
<meta charset="utf-8">
<title>brightkeyhomes stationery pack</title>
<link rel="stylesheet" href="https://fonts.googleapis.com/css2?family=Open+Sans:ital,wght@0,400;0,600;1,400&display=swap">
<style>
:root{
  --bg:#e9e7e3;
  --paper:#ffffff;
  --ink:#2d3142;
  --muted:#555a66;
  --green:#2f9a47;
  --blue:#1f76bb;
  --purple:#6b2d86;
  --red:#d3242a;
  --black:#0c0c0c;
  --line:#8a8a8a;
  --mark:#1f76bb;
}
*{box-sizing:border-box;margin:0;padding:0}
html,body{width:1200px;height:900px;overflow:hidden}
body{background:var(--bg);font-family:"Open Sans",Arial,sans-serif;color:var(--ink);position:relative}
.sheet{position:absolute;background:var(--paper);overflow:hidden;box-shadow:0 2px 6px rgba(0,0,0,.18)}
.band{position:absolute;left:0;bottom:0;width:100%;background:linear-gradient(100deg,var(--green) 0%,var(--blue) 45%,var(--purple) 80%,var(--red) 100%)}
.brand{display:flex;align-items:center;gap:.35em;font-weight:600;color:var(--ink);white-space:nowrap}
.brand::before{content:"";width:1.1em;height:1.1em;border-radius:50%;background:var(--mark);flex:none}
.contact{position:absolute;list-style:none;font-size:5px;line-height:1.5;color:var(--muted)}
.contact li{display:flex;align-items:center;gap:3px;white-space:nowrap}
.contact .cont{padding-left:8px}
.ico{width:1em;height:1em;flex:none;fill:var(--green)}
.web-foot{position:absolute;left:25px;bottom:8px;font-size:5px;color:#fff}

.letterhead-a{left:18px;top:55px;width:272px;height:385px}
.letterhead-a .brand{position:absolute;left:26px;top:60px;font-size:13px}
.letterhead-a .contact{left:176px;top:34px}
.letterhead-b{left:304px;top:45px;width:290px;height:412px}
.letterhead-b .brand{position:absolute;left:0;right:0;top:84px;justify-content:center;font-size:17px}

.fax{top:55px;width:276px;height:388px}
.fax-a{left:611px}.fax-b{left:904px}
.fax .brand{position:absolute;left:18px;top:50px;font-size:10px}
.fax .contact{left:196px;top:30px;font-size:4.5px}
.fax-title{position:absolute;right:16px;top:82px;font-weight:600;font-size:9px;color:#444}
.fax-grid{position:absolute;left:18px;top:96px;width:243px;border-collapse:collapse;font-size:5px;table-layout:fixed}
.fax-grid td{border:1px solid var(--line);height:11px;padding:0 3px}
.fax-grid td.lbl{background:#f1f1f1}
.fax-checks{position:absolute;left:18px;top:162px;width:243px;border-collapse:collapse;font-size:5px;text-align:center;table-layout:fixed}
.fax-checks th{font-weight:400;border:1px solid var(--line);background:#e4e4e4;height:11px}
.fax-checks td{border:1px solid var(--line);height:168px;vertical-align:top;padding-top:6px}
.check-row{position:absolute;left:18px;top:148px;display:flex;gap:12px;font-size:5px;color:#444}
.check-row span{display:flex;align-items:center;gap:3px}
.check-row span::before{content:"";width:6px;height:6px;border:1px solid var(--line)}

.card{position:absolute;overflow:hidden;border-radius:10px;box-shadow:0 2px 6px rgba(0,0,0,.2)}
.card-front{left:25px;top:490px;width:265px;height:152px;background:var(--paper)}
.card-front .brand{position:absolute;left:20px;top:78px;font-size:12px}
.card-person{position:absolute;left:150px;top:38px;font-size:9px;line-height:1.2}
.card-person .name{color:var(--red);font-weight:600}
.card-person .role{color:var(--blue)}
.card-person .mobile{font-size:6px;color:var(--muted)}
.card-front .contact{left:150px;top:76px;font-size:6.5px}
.card-back{left:309px;top:490px;width:275px;height:157px;background:var(--black)}
.card-back .brand{position:absolute;left:0;right:0;top:93px;justify-content:center;font-size:15px;color:#fff}
.card-back .site{position:absolute;left:0;right:0;top:137px;text-align:center;font-size:6.5px;color:#ddd}
.card-back .site b{font-weight:400;color:var(--green)}

.slip{left:64px;top:662px;width:434px;height:205px}
.slip .brand{position:absolute;left:52px;top:74px;font-size:15px}
.slip-note{position:absolute;right:26px;top:40px;font-style:italic;font-size:12px;color:#444}

.envelope{position:absolute;background:var(--paper);box-shadow:0 2px 6px rgba(0,0,0,.2);overflow:hidden}
.envelope .flap{position:absolute;left:0;top:0;width:100%;height:70px;display:block}
.env-blue{left:600px;top:480px;width:470px;height:205px}
.env-red{left:644px;top:556px;width:484px;height:210px}
.flap-mark{position:absolute;top:22px;width:34px;height:34px;border-radius:50%;background:#fff}
.env-blue .flap-mark{left:218px;top:18px}
.env-red .flap-mark{left:225px}
.env-front{left:686px;top:642px;width:474px;height:205px}
.env-front .brand{position:absolute;left:60px;top:58px;font-size:13px}
.env-front .contact{left:334px;top:34px;font-size:6.5px}
.env-window{position:absolute;left:28px;top:93px;width:155px;height:42px;border:1px solid #aaa;border-radius:6px;background:linear-gradient(#f4f4f4,#d9d9d9)}
</style>
</head>
<body>

<svg width="0" height="0" style="position:absolute" aria-hidden="true">
  <defs>
    <symbol id="i-pin" viewBox="0 0 10 10"><path d="M5 0a3.5 3.5 0 0 0-3.5 3.5C1.5 6 5 10 5 10s3.5-4 3.5-6.5A3.5 3.5 0 0 0 5 0zm0 5a1.5 1.5 0 1 1 0-3 1.5 1.5 0 0 1 0 3z"/></symbol>
    <symbol id="i-phone" viewBox="0 0 10 10"><path d="M2 1l2 0 1 2.5-1.3 1a6 6 0 0 0 2.8 2.8l1-1.3L10 7v2c0 .6-.4 1-1 1A9 9 0 0 1 0 1c0-.6.4-1 1-1z"/></symbol>
    <symbol id="i-mail" viewBox="0 0 10 10"><path d="M0 2h10v6H0z M0 2l5 3.5L10 2" stroke="#fff" stroke-width=".8"/></symbol>
    <symbol id="i-web" viewBox="0 0 10 10"><circle cx="5" cy="5" r="5"/><path d="M0 5h10M5 0v10" stroke="#fff" stroke-width=".7"/></symbol>
  </defs>
</svg>

<section class="sheet letterhead-a" aria-label="Letterhead">
  <div class="brand">brightkeyhomes</div>
  <ul class="contact">
    <li><svg class="ico"><use href="#i-pin"/></svg>Shop 4, 212 harbour road,</li>
    <li class="cont">merridale qld 4581</li>
    <li><svg class="ico"><use href="#i-phone"/></svg>07 5210 4637</li>
    <li><svg class="ico"><use href="#i-mail"/></svg>marcus@brightkeyhomes.com.au</li>
    <li><svg class="ico"><use href="#i-web"/></svg>www.brightkeyhomes.com.au</li>
  </ul>
  <div class="band" style="height:44px" role="img" aria-label="Decorative wave band in green, blue, purple and red"></div>
</section>

<section class="sheet letterhead-b" aria-label="Letterhead cover">
  <div class="brand">brightkeyhomes</div>
  <div class="band" style="height:115px" role="img" aria-label="Decorative wave band in green, blue, purple and red"></div>
  <p class="web-foot">www.brightkeyhomes.com.au</p>
</section>

<section class="sheet fax fax-a" aria-label="Fax header">
  <div class="brand">brightkeyhomes</div>
  <ul class="contact">
    <li><svg class="ico"><use href="#i-pin"/></svg>Shop 4, 212 harbour road,</li>
    <li class="cont">merridale qld 4581</li>
    <li><svg class="ico"><use href="#i-phone"/></svg>07 5210 4637</li>
    <li><svg class="ico"><use href="#i-mail"/></svg>marcus@brightkeyhomes.com.au</li>
    <li><svg class="ico"><use href="#i-web"/></svg>www.brightkeyhomes.com.au</li>
  </ul>
  <p class="fax-title">FAX</p>
  <table class="fax-grid">
    <tr><td class="lbl">To:</td><td></td><td class="lbl">From:</td><td></td></tr>
    <tr><td class="lbl">Fax:</td><td></td><td class="lbl">Pages:</td><td></td></tr>
    <tr><td class="lbl">Phone:</td><td></td><td class="lbl">Date:</td><td></td></tr>
    <tr><td class="lbl">Re:</td><td></td><td class="lbl">CC:</td><td></td></tr>
  </table>
  <table class="fax-checks">
    <tr><th>Urgent</th><th>For Review</th><th>Please comment</th><th>Please Reply</th><th>Please Recycle</th></tr>
    <tr><td colspan="5">COMMENTS</td></tr>
  </table>
  <div class="band" style="height:44px" role="img" aria-label="Decorative wave band in green, blue, purple and red"></div>
</section>

<section class="sheet fax fax-b" aria-label="Fax header">
  <div class="brand">brightkeyhomes</div>
  <ul class="contact">
    <li><svg class="ico"><use href="#i-pin"/></svg>Shop 4, 212 harbour road,</li>
    <li class="cont">merridale qld 4581</li>
    <li><svg class="ico"><use href="#i-phone"/></svg>07 5210 4637</li>
    <li><svg class="ico"><use href="#i-mail"/></svg>marcus@brightkeyhomes.com.au</li>
    <li><svg class="ico"><use href="#i-web"/></svg>www.brightkeyhomes.com.au</li>
  </ul>
  <p class="fax-title">FAX</p>
  <table class="fax-grid">
    <tr><td class="lbl">To:</td><td></td><td class="lbl">From:</td><td></td></tr>
    <tr><td class="lbl">Fax:</td><td></td><td class="lbl">Pages:</td><td></td></tr>
    <tr><td class="lbl">Phone:</td><td></td><td class="lbl">Date:</td><td></td></tr>
    <tr><td class="lbl">Re:</td><td></td><td class="lbl">CC:</td><td></td></tr>
  </table>
  <div class="check-row"><span>Urgent</span><span>For Review</span><span>Please comment</span><span>Please Reply</span><span>Please Recycle</span></div>
  <div class="band" style="height:44px" role="img" aria-label="Decorative wave band in green, blue, purple and red"></div>
</section>

<section class="card card-front" aria-label="Business card front">
  <div class="brand">brightkeyhomes</div>
  <div class="card-person">
    <p class="name">Marcus Delaney</p>
    <p class="role">Principal</p>
    <p class="mobile">0427815694</p>
  </div>
  <ul class="contact">
    <li><svg class="ico"><use href="#i-pin"/></svg>shop 4, 212 harbour road,</li>
    <li class="cont" style="padding-left:9px">merridale qld 4581</li>
    <li><svg class="ico"><use href="#i-phone"/></svg>07 5210 4637</li>
    <li><svg class="ico"><use href="#i-mail"/></svg>marcus@brightkeyhomes.com.au</li>
    <li><svg class="ico"><use href="#i-web"/></svg>www.brightkeyhomes.com.au</li>
  </ul>
  <div class="band" style="height:26px" role="img" aria-label="Decorative wave band in green, blue, purple and red"></div>
</section>

<section class="card card-back" aria-label="Business card back">
  <div class="brand">brightkeyhomes</div>
  <p class="site">www.<b>brightkeyhomes</b>.com.au</p>
</section>

<section class="sheet slip" aria-label="With compliments slip">
  <div class="brand">brightkeyhomes</div>
  <p class="slip-note">With Compliments</p>
  <div class="band" style="height:60px" role="img" aria-label="Decorative wave band in green, blue, purple and red"></div>
</section>

<section class="envelope env-blue" aria-label="Envelope back with blue flap">
  <svg class="flap" viewBox="0 0 470 70" preserveAspectRatio="none"><path d="M0,0 H470 V8 C440,8 430,20 380,36 C330,52 300,62 235,62 C170,62 140,52 90,36 C40,20 30,8 0,8 Z" fill="var(--blue)"/></svg>
  <span class="flap-mark"></span>
</section>

<section class="envelope env-red" aria-label="Envelope back with red flap">
  <svg class="flap" viewBox="0 0 484 70" preserveAspectRatio="none"><path d="M0,0 H484 V8 C454,8 444,20 394,36 C344,52 314,66 242,66 C170,66 140,52 90,36 C40,20 30,8 0,8 Z" fill="var(--red)"/></svg>
  <span class="flap-mark"></span>
</section>

<section class="envelope env-front" aria-label="Envelope front">
  <div class="brand">brightkeyhomes</div>
  <ul class="contact">
    <li><svg class="ico"><use href="#i-pin"/></svg>Shop 4, 212 harbour road,</li>
    <li class="cont" style="padding-left:9px">merridale qld 4581</li>
    <li><svg class="ico"><use href="#i-phone"/></svg>07 5210 4637</li>
    <li><svg class="ico"><use href="#i-mail"/></svg>marcus@brightkeyhomes.com.au</li>
    <li><svg class="ico"><use href="#i-web"/></svg>www.brightkeyhomes.com.au</li>
  </ul>
  <div class="env-window"></div>
  <div class="band" style="height:58px" role="img" aria-label="Decorative wave band in green, blue, purple and red"></div>
</section>

</body>
</html>
```